VORNAK SYSTEMS BUSINESS CARD DESIGN

WE WANT COMPLETE NEW DESIGN OF OUR BUSINESS CARD. WE ARE AN INTEGRATION COMPANY, WHERE WE INTEGRATE IOT/SMART SYSTEMS TO HOMES AND CORPORATE CUSTOMERS. WE SUPPLY AND INSTALL AUTOMATION PRODUCTS. THE FINAL DESIGN SHOULD COMMUNICATE TECHNOLOGY. THE CARD DESIGN SHOULD BE VERY IMPACT FULL. LOGO NEEDS TO BE THERE. IT WOULD NICE IF THE DESIGN WAS CLEAN. COLORS IS UP TO DESIGNER TO PLAY WITH, OR CAN STICK TO CORPORATE COLORS (FOLLOW LOGO). I HAVE ADDED FEW REFERENCE PHOTOS TO DRAW INSPIRATION MAYBE. I HAVE ADDED A HEX DESIGN, ITS NOT NECESSARY TO USE THIS DESIGN, ITS UPTO DESIGNER, JUST ADDED IF NEEDED TO PLAY WITH DESIGN.

Target Market(s)

Private end users and corporate clients

Industry/Entity Type

technology, home automation, home theaters, building management systems, IOT

Contact Information for Business Card

It should include Employee name, personal number, office number, email address, both in English and arabic. DETAILS TO INCLUDE :RAJESH PALLIVAL, MOBILE 0097150738265,OFFCIE 009714368547, RAJESH@VORNAKSYS.EXAMPLE

Requirements
Must have
• Should feel like a technology company from design. Details both and in English and arabic (or at least have provision for arabic in design).
Nice to have
• I would like logo on one side, and details on the other side. Logo design side should communicate technology with logo. Other side can be clean just with information or also have some design aspects following from logo side. it would be interesting to see submissions with square design as well (that looks like an app Icon). colors could be of logo, red black grey and white. I have added some designs to draw inspiration from

```html
<!DOCTYPE html>
<html lang="en">
<head>
<meta charset="utf-8">
<title>Vornak Systems – Business Card</title>
<link rel="stylesheet" href="https://fonts.googleapis.com/css2?family=Michroma&family=Roboto:wght@400&family=Roboto+Condensed:wght@400;500;700&display=swap">
<style>
  :root{
    --backdrop:#2a2a2a;
    --card:#efefef;
    --card-shade:#dedede;
    --ink:#111111;
    --grey:#8c8c8c;
    --red:#d3141f;
  }
  *{margin:0;padding:0;box-sizing:border-box}
  html,body{width:1200px;height:1138px;overflow:hidden;background:var(--backdrop)}
  .sheet{position:relative;width:1200px;height:1138px}
  .card{
    position:absolute;width:620px;height:375px;border-radius:16px;overflow:hidden;
    background:linear-gradient(160deg,#f7f7f7 0%,var(--card) 55%,var(--card-shade) 100%);
  }
  .card--front{left:272px;top:184px}
  .card--back{left:274px;top:606px}

  .brand{position:absolute;z-index:2;font-family:"Roboto Condensed",sans-serif}
  .brand__row{display:flex;align-items:center;gap:10px}
  .brand__dot{width:30px;height:30px;border-radius:50%;background:var(--red);flex:none}
  .brand__name{font-weight:700;font-size:38px;line-height:1;letter-spacing:2px;color:var(--ink)}
  .brand__sub{font-weight:400;font-size:17px;color:var(--grey);letter-spacing:.5px;margin-top:2px;padding-left:40px}
  .brand__tagline{font-family:"Michroma",sans-serif;font-size:10px;letter-spacing:1.6px;color:var(--ink);margin-top:8px;white-space:nowrap}

  .card--front .brand{left:46px;top:100px}
  .card--back .brand{right:30px;top:42px;text-align:right}
  .card--back .brand__row{justify-content:flex-end}

  .facets{position:absolute;left:0;top:0}

  .holder{position:absolute;right:36px;top:168px;text-align:right;
    font-family:"Roboto Condensed",sans-serif;font-weight:500;font-size:26px;color:var(--red)}
  .contacts{position:absolute;right:22px;top:246px;list-style:none;
    font-family:"Roboto",sans-serif;font-size:17px;color:var(--ink)}
  .contacts li{display:flex;align-items:center;justify-content:flex-end;gap:8px;height:24px}
  .contacts svg{width:14px;height:14px;flex:none}
</style>
</head>
<body>
<main class="sheet">

  <section class="card card--front" aria-label="Card front">
    <svg class="facets" width="620" height="375" viewBox="0 0 620 375">
      <defs>
        <linearGradient id="facetFront" x1="0" y1="0" x2="1" y2="1">
          <stop offset="0" stop-color="#2fc7a8"/>
          <stop offset=".3" stop-color="#e6d21c"/>
          <stop offset=".5" stop-color="#f2a516"/>
          <stop offset=".72" stop-color="#e0262f"/>
          <stop offset="1" stop-color="#3a4fa8"/>
        </linearGradient>
      </defs>
      <path role="img" aria-label="Multicoloured faceted stained-glass pattern" d="M400 54 H584 V322 H204 Z" fill="url(#facetFront)"/>
    </svg>
    <div class="brand">
      <div class="brand__row"><span class="brand__dot"></span><span class="brand__name">VORNAK</span></div>
      <div class="brand__sub">SYSTEMS L.L.C</div>
      <div class="brand__tagline">A VORNAK GROUP DIVISION.</div>
    </div>
  </section>

  <section class="card card--back" aria-label="Card back">
    <svg class="facets" width="620" height="375" viewBox="0 0 620 375">
      <defs>
        <linearGradient id="facetFill" x1="0" y1="0" x2="1" y2="1">
          <stop offset="0" stop-color="#2a3f8f"/>
          <stop offset=".3" stop-color="#f29a16"/>
          <stop offset=".55" stop-color="#e6c81c"/>
          <stop offset=".8" stop-color="#e0262f"/>
          <stop offset="1" stop-color="#2fae8a"/>
        </linearGradient>
      </defs>
      <path d="M221 0 Q356 187 230 375" fill="none" stroke="var(--red)" stroke-width="9"/>
      <path role="img" aria-label="Multicoloured faceted stained-glass pattern" d="M0 0 H213 Q346 187 222 375 H0 Z" fill="url(#facetFill)"/>
    </svg>

    <div class="brand">
      <div class="brand__row"><span class="brand__dot"></span><span class="brand__name">VORNAK</span></div>
      <div class="brand__sub">SYSTEMS L.L.C</div>
      <div class="brand__tagline">A VORNAK GROUP DIVISION.</div>
    </div>

    <div class="holder">Rajesh Pallival</div>

    <ul class="contacts">
      <li>0097150738265
        <svg viewBox="0 0 14 14"><rect x="3.5" y="1" width="7" height="12" rx="1.5" fill="none" stroke="var(--red)" stroke-width="1.4"/><circle cx="7" cy="10.5" r=".9" fill="var(--red)"/></svg></li>
      <li>009714368547
        <svg viewBox="0 0 14 14"><circle cx="7" cy="7" r="6" fill="none" stroke="var(--red)" stroke-width="1.3"/><path d="M5 4.2 L6 6 L5.3 6.8 Q6.2 8.4 7.3 8.9 L8.1 8.2 L9.8 9.2 L9.3 10.2 Q6.5 10.4 4.2 6 Z" fill="var(--red)"/></svg></li>
      <li>rajesh@vornaksys.example
        <svg viewBox="0 0 14 14"><rect x="1" y="3" width="12" height="8.5" fill="none" stroke="var(--red)" stroke-width="1.3"/><path d="M1 3 L7 8 L13 3" fill="none" stroke="var(--red)" stroke-width="1.3"/></svg></li>
      <li>www.vornaksys.example
        <svg viewBox="0 0 14 14"><circle cx="7" cy="7" r="6" fill="none" stroke="var(--red)" stroke-width="1.3"/><ellipse cx="7" cy="7" rx="2.6" ry="6" fill="none" stroke="var(--red)" stroke-width="1.1"/><path d="M1 7 H13 M2 4 H12 M2 10 H12" stroke="var(--red)" stroke-width="1"/></svg></li>
    </ul>
  </section>

</main>
</body>
</html>
```